Brintel Works - Fast, Efficient and Gas Mainteance for Domestic, Commercial and Industrial clients

We are in the process of purchasing a new business and would like to get a new logo and business card.
Business is a gas maintenance business that also does new gas installations.
Has been established since 1988.
Services include:
Install all types of gas appliances & equipment inc. hot water units
Maintain / repair / replace all types of gas appliances & equipment

Target Market(s)

Domestic, Commercial and Industrial clients

Industry/Entity Type

Business

Contact Information for Business Card

admin@brintelworks.com.au
07 3918 4726
Brintel Works PTY LTD

Logo Text

Gas Fitting & Plumbing Maintenance Specialists

Font styles to use
Sans Serif

Requirements
Must have
• Logo
• Business name, contact number, email address, web address
• Domestic | Commercial | Industrial Est Since 1988
Nice to have
• Possibly a black card with a flame logo to one side
Should not have
• Spelling errors

```html
<!DOCTYPE html>
<html lang="en">
<head>
<meta charset="utf-8">
<title>Brintel Works – Business Card</title>
<link href="https://fonts.googleapis.com/css2?family=Libre+Baskerville:wght@700&family=Open+Sans:wght@400;600&family=Great+Vibes&display=swap" rel="stylesheet">
<style>
  :root{
    --bg:#e9e7e3;
    --card:#f7f7f6;
    --red:#ea4a33;
    --red-deep:#d93b26;
    --brand-red:#e0523c;
    --ink:#4a4d52;
    --ink-soft:#6b6e73;
    --faint:#d5d5d5;
    --edge:#c9c9c9;
    --white:#ffffff;
  }
  *{margin:0;padding:0;box-sizing:border-box}
  html,body{width:1200px;height:892px;overflow:hidden;background:var(--bg)}
  .canvas{position:relative;width:1200px;height:892px}
  .card{
    position:absolute;left:280px;width:640px;height:366px;
    background:var(--card);overflow:hidden;
    box-shadow:0 6px 18px rgba(0,0,0,.18);
  }
  .card--front{top:50px}
  .card--back{top:476px}

  /* front */
  .front__mark{position:absolute;left:64px;top:58px;width:170px;height:250px;border-radius:50%;background:var(--faint);opacity:.7}
  .front__text{position:absolute;left:250px;top:150px}
  .brand-name{font-family:"Libre Baskerville",serif;font-weight:700;color:var(--brand-red);text-transform:uppercase;letter-spacing:.5px;white-space:nowrap}
  .front__text .brand-name{font-size:36px;line-height:1}
  .tagline{font-family:"Open Sans",sans-serif;font-weight:600;color:var(--ink);white-space:nowrap}
  .front__text .tagline{font-size:21px;margin-top:10px}
  .sectors{font-family:"Open Sans",sans-serif;color:var(--ink-soft);display:flex;align-items:baseline;gap:14px;white-space:nowrap}
  .front__text .sectors{font-size:13px;margin-top:14px}
  .established{font-family:"Great Vibes",cursive;color:var(--ink-soft)}
  .front__text .established{font-size:20px}

  /* back */
  .back__shapes{position:absolute;inset:0}
  .back__mark{position:absolute;border-radius:50%;background:var(--faint);opacity:.7}
  .back__mark--top{left:330px;top:8px;width:56px;height:74px}
  .back__mark--side{left:568px;top:148px;width:56px;height:74px}
  .back__brand{position:absolute;right:22px;top:62px;text-align:left}
  .back__brand .brand-name{font-size:18px;line-height:1.1}
  .back__brand .pty{font-family:"Open Sans",sans-serif;font-size:6px;font-weight:600;color:var(--ink);margin-left:4px;letter-spacing:0}
  .back__brand .tagline{font-size:11px;margin-top:4px}
  .back__brand .sectors{font-size:7px;margin-top:4px;gap:6px}
  .back__brand .established{font-size:11px}
  .contact{position:absolute;left:40px;top:48px;list-style:none;font-family:"Open Sans",sans-serif;color:var(--white);font-size:19px}
  .contact li{display:flex;align-items:center;gap:14px;height:30px}
  .contact svg{width:16px;height:16px;flex:none}
  .products{
    position:absolute;left:396px;top:246px;width:132px;height:104px;border-radius:6px;
    background:linear-gradient(135deg,#4b4d50 0%,#7a7c80 45%,#c9cbcf 100%);
  }
</style>
</head>
<body>
<main class="canvas">

  <section class="card card--front" aria-label="Card front">
    <div class="front__mark" aria-hidden="true"></div>
    <div class="front__text">
      <p class="brand-name">Brintel Works</p>
      <p class="tagline">Gas fitting &amp; Plumbing Specialists</p>
      <p class="sectors"><span>Domestic | Commercial | Industrial</span><span class="established">Est Since 1988</span></p>
    </div>
  </section>

  <section class="card card--back" aria-label="Card back">
    <svg class="back__shapes" viewBox="0 0 640 366" aria-hidden="true">
      <polygon points="0,0 220,0 246,40 640,303 640,366 0,366" fill="var(--red)"/>
      <polyline points="230,0 256,40 640,296" fill="none" stroke="var(--edge)" stroke-width="6"/>
      <polygon points="0,190 0,366 300,366" fill="var(--red-deep)" opacity=".25"/>
    </svg>
    <div class="back__mark back__mark--top" aria-hidden="true"></div>
    <div class="back__mark back__mark--side" aria-hidden="true"></div>
    <div class="back__brand">
      <p class="brand-name">Brintel Works<span class="pty">PTY LTD</span></p>
      <p class="tagline">Gas fitting &amp; Plumbing Specialists</p>
      <p class="sectors"><span>Domestic | Commercial | Industrial</span><span class="established">Est Since 1988</span></p>
    </div>
    <ul class="contact">
      <li>
        <svg viewBox="0 0 16 16" aria-hidden="true"><rect width="16" height="16" rx="2" fill="#fff"/><path d="M5 3.5l2 2-1 1.2c.6 1.3 1.6 2.3 2.9 2.9l1.2-1 2 2-1.3 1.4C7.5 12 4 8.5 3.6 5z" fill="var(--red)"/></svg>
        <span>07 3918 4726</span>
      </li>
      <li>
        <svg viewBox="0 0 16 16" aria-hidden="true"><rect width="16" height="16" rx="2" fill="#fff"/><rect x="3" y="4.5" width="10" height="7" fill="none" stroke="var(--red)" stroke-width="1.3"/><path d="M3 4.5l5 4 5-4" fill="none" stroke="var(--red)" stroke-width="1.3"/></svg>
        <span>admin@brintelworks.com.au</span>
      </li>
      <li>
        <svg viewBox="0 0 16 16" aria-hidden="true"><rect width="16" height="16" rx="2" fill="#fff"/><circle cx="8" cy="8" r="4.6" fill="none" stroke="var(--red)" stroke-width="1.2"/><path d="M3.4 8h9.2M8 3.4c-2.4 2.6-2.4 6.6 0 9.2M8 3.4c2.4 2.6 2.4 6.6 0 9.2" fill="none" stroke="var(--red)" stroke-width="1"/></svg>
        <span>www.brintelworks.com.au</span>
      </li>
    </ul>
    <div class="products" role="img" aria-label="Product photo of a gas log heater with glowing fire and two hot water units"></div>
  </section>

</main>
</body>
</html>
```